The Marrowby Hotel Flyer

it is for a Pub that has been in the area for a long time but now we have changed the name and taken over as new owners and now have to try to get all the locals back, eating and drinking..

This Flyer is to try get all the locals to come try the new Marrowby Hotel.

We have a great new menu with daily food deals
Craft beers
Week nights Live music
Tuesday Comedy night
Sunday live music

Industry/Entity Type

Hotel

```html
<!DOCTYPE html>
<html lang="en">
<head>
<meta charset="utf-8">
<title>The Marrowby Hotel Flyer</title>
<link rel="stylesheet" href="https://fonts.googleapis.com/css2?family=Anton&family=Arimo:wght@400&family=Roboto+Condensed:wght@400&display=swap">
<style>
  :root {
    --navy: #0b1868;
    --ribbon: #2f3b98;
    --ribbon-tail: #1d2a85;
    --badge-light: #5a66c0;
    --badge-dark: #1f2b86;
    --paper: #ffffff;
    --glass-edge: #d3d6db;
    --glass-light: #fbfbfc;
    --glass-mid: #eceef1;
  }
  * { margin: 0; padding: 0; box-sizing: border-box; }
  html, body { width: 848px; height: 1200px; overflow: hidden; background: var(--paper); }
  .flyer { position: relative; width: 848px; height: 1200px; overflow: hidden; background: var(--paper); }
  .shapes { position: absolute; inset: 0; }
  .brand {
    position: absolute; top: 150px; left: 0; width: 100%;
    text-align: center; color: var(--navy);
    font-family: "Arimo", Arial, sans-serif; font-weight: 400;
    font-size: 74px; letter-spacing: 2px; text-transform: uppercase; line-height: 1.1;
  }
  .intro, .joiner {
    position: absolute; left: 108px; color: var(--navy);
    font-family: "Arimo", Arial, sans-serif; font-size: 35px;
  }
  .intro { top: 374px; }
  .joiner { top: 527px; }
  .headline {
    position: absolute; left: 108px; color: var(--navy);
    font-family: "Anton", Impact, sans-serif; font-size: 64px; line-height: 1;
    text-shadow: 2px 2px 2px rgba(0,0,0,0.35);
  }
  .headline.menu { top: 436px; }
  .headline.beers { top: 592px; }
  .badge {
    position: absolute; left: 556px; top: 372px; width: 200px; height: 200px;
    clip-path: polygon(100% 50%, 89.6% 60.6%, 93.3% 75%, 79% 79%, 75% 93.3%, 60.6% 89.6%, 50% 100%, 39.4% 89.6%, 25% 93.3%, 21% 79%, 6.7% 75%, 10.4% 60.6%, 0% 50%, 10.4% 39.4%, 6.7% 25%, 21% 21%, 25% 6.7%, 39.4% 10.4%, 50% 0%, 60.6% 10.4%, 75% 6.7%, 79% 21%, 93.3% 25%, 89.6% 39.4%);
    background: radial-gradient(circle at 45% 40%, var(--badge-light), var(--badge-dark) 75%);
    transform: rotate(-6deg);
    display: flex; flex-direction: column; align-items: center; justify-content: center;
  }
  .badge span {
    color: var(--paper); font-family: "Arimo", Arial, sans-serif; font-weight: 400;
    font-size: 30px; line-height: 1.4; letter-spacing: 3px;
    text-shadow: 2px 2px 2px rgba(0,0,0,0.6);
  }
  .schedule {
    position: absolute; left: 0; width: 100%; text-align: center; color: var(--navy);
    font-family: "Roboto Condensed", "Arial Narrow", sans-serif; font-size: 42px;
  }
  .schedule.weeknights { top: 722px; }
  .schedule.tuesday { top: 918px; }
  .ribbon-label {
    position: absolute; left: 172px; width: 490px; text-align: center;
    font-family: "Anton", Impact, sans-serif; font-size: 68px; line-height: 1;
    color: var(--paper);
    text-shadow: 3px 3px 2px rgba(0,0,0,0.55);
  }
  .ribbon-label.music { top: 806px; }
  .ribbon-label.comedy { top: 990px; }
</style>
</head>
<body>
<main class="flyer">
  <svg class="shapes" width="848" height="1200" viewBox="0 0 848 1200" aria-hidden="false">
    <defs>
      <linearGradient id="glassFill" x1="0" x2="1" y1="0" y2="0">
        <stop offset="0" stop-color="var(--glass-mid)"/>
        <stop offset="0.2" stop-color="var(--glass-light)"/>
        <stop offset="0.8" stop-color="var(--glass-light)"/>
        <stop offset="1" stop-color="var(--glass-mid)"/>
      </linearGradient>
    </defs>
    <path class="pint-glass" role="img" aria-label="Clear pint glass illustration"
      d="M18 0 L830 0 Q826 200 808 330 Q790 460 800 560 Q812 680 780 900 L760 1200 L88 1200 L68 900 Q36 680 48 560 Q58 460 40 330 Q22 200 18 0Z"
      fill="url(#glassFill)" stroke="var(--glass-edge)" stroke-width="3"/>
    <g class="ribbon music-ribbon">
      <polygon points="122,832 205,832 205,916 122,916 148,874" fill="var(--ribbon-tail)"/>
      <polygon points="630,832 714,832 688,874 714,916 630,916" fill="var(--ribbon-tail)"/>
      <rect x="172" y="800" width="490" height="90" fill="var(--ribbon)"/>
    </g>
    <g class="ribbon comedy-ribbon">
      <polygon points="122,1016 205,1016 205,1100 122,1100 148,1058" fill="var(--ribbon-tail)"/>
      <polygon points="630,1016 714,1016 688,1058 714,1100 630,1100" fill="var(--ribbon-tail)"/>
      <rect x="172" y="984" width="490" height="90" fill="var(--ribbon)"/>
    </g>
  </svg>

  <h1 class="brand">The Marrowby Hotel</h1>

  <p class="intro">Come try our</p>
  <h2 class="headline menu">Great New Menu</h2>
  <p class="joiner">and</p>
  <h2 class="headline beers">Craft Beers</h2>

  <div class="badge"><span>Daily</span><span>Food</span><span>Deals</span></div>

  <p class="schedule weeknights">Week Nights + Sunday</p>
  <p class="ribbon-label music">Live Music</p>
  <p class="schedule tuesday">Tuesday</p>
  <p class="ribbon-label comedy">Comedy Night</p>
</main>
</body>
</html>
```